Landscape design build company door flyer

I would like this flyer to convey a high-level of professionalism for a company that is excellent with communication with their clients as well as a company that does incredible installations

Went on vacation/holiday

```html
<!DOCTYPE html>
<html lang="en">
<head>
<meta charset="UTF-8">
<title>Cedarstone Builders – Outdoor Living Flyer</title>
<link href="https://fonts.googleapis.com/css2?family=Barlow+Semi+Condensed:wght@700&family=Montserrat:wght@400;600;700;800&display=swap" rel="stylesheet">
<style>
  :root{
    --navy:#1b3247;
    --navy-deep:#162a3c;
    --navy-glow:#1f5a78;
    --orange:#ee7a22;
    --ink:#1e3447;
    --rule:#b9bcbf;
    --paper:#ffffff;
    --backdrop:#e6e6e6;
  }
  *{margin:0;padding:0;box-sizing:border-box;}
  html,body{width:1200px;height:1029px;overflow:hidden;background:var(--backdrop);}
  .flyer{
    position:absolute;left:211px;top:14px;width:778px;height:1001px;
    background:var(--paper);overflow:hidden;
    font-family:"Montserrat",sans-serif;color:var(--ink);
  }
  .info-column{position:absolute;left:0;top:0;width:332px;height:1001px;}
  .brand{position:absolute;left:0;top:68px;width:292px;text-align:center;}
  .brand-dot{display:block;width:58px;height:58px;border-radius:50%;background:var(--orange);margin:0 auto 14px;}
  .brand-name{font-family:"Montserrat",sans-serif;font-weight:600;font-size:17px;color:var(--orange);letter-spacing:.5px;}
  .headline{
    position:absolute;left:38px;top:184px;
    font-family:"Barlow Semi Condensed",sans-serif;font-weight:700;
    font-size:41px;line-height:37px;color:var(--ink);text-transform:uppercase;
  }
  .divider{position:absolute;left:38px;top:353px;width:261px;height:1px;background:var(--rule);}
  .divider::before{content:"";position:absolute;left:0;top:-0.5px;width:126px;height:2px;background:var(--orange);}
  .intro{
    position:absolute;left:38px;top:369px;width:262px;
    font-size:12.1px;line-height:14.9px;text-align:justify;color:var(--ink);
  }
  .services{position:absolute;left:38px;top:479px;list-style:none;}
  .services li{
    position:relative;height:34.6px;padding-left:10px;
    font-weight:700;font-size:16px;line-height:19px;color:var(--ink);letter-spacing:.2px;
  }
  .services li::before{content:"";position:absolute;left:0;top:0;width:2px;height:19px;background:var(--orange);}
  .contact-panel{
    position:absolute;left:0;top:728px;width:332px;height:273px;
    background:radial-gradient(ellipse 180px 130px at 130px 150px,var(--navy-glow) 0%,var(--navy) 70%,var(--navy-deep) 100%);
    color:#fff;
  }
  .areas{position:absolute;left:38px;top:16px;width:270px;font-size:12px;line-height:18.4px;font-weight:400;}
  .areas strong{font-weight:700;}
  .contact-tag{position:absolute;left:38px;top:107px;width:253px;height:22px;}
  .contact-tag .line{position:absolute;left:160px;top:10.5px;width:93px;height:1px;background:var(--orange);}
  .contact-tag svg{position:absolute;left:0;top:0;}
  .contact-tag span{position:absolute;left:8px;top:3px;font-weight:800;font-size:14px;letter-spacing:4.2px;color:#fff;}
  .phone{position:absolute;left:41px;top:146px;display:flex;align-items:center;gap:16px;}
  .phone-number{font-weight:800;font-size:25px;letter-spacing:1.4px;}
  .contact-line{position:absolute;left:43px;display:flex;align-items:center;gap:15px;font-size:12.6px;}
  .contact-line.email{top:186px;}
  .contact-line.web{top:208px;}
  .gallery{position:absolute;left:335px;top:0;width:443px;height:1001px;}
  .photo{position:absolute;left:0;width:443px;height:248px;}
  .photo.deck{top:0;background:linear-gradient(180deg,#9a9994 0%,#8a7a66 25%,#9c7a5c 45%,#8b6a4f 65%,#a48a6c 100%);}
  .photo.patio-cover{top:251px;width:430px;background:linear-gradient(180deg,#b9c9d6 0%,#a5935c 30%,#6b4e36 50%,#3f4650 70%,#9a9d9c 100%);}
  .photo.pavilion{top:502px;background:linear-gradient(180deg,#a8c5de 0%,#6f7a58 30%,#7b5a3d 45%,#4c5359 70%,#55606b 100%);}
  .photo.hillside{top:753px;background:linear-gradient(170deg,#7c6e5c 0%,#4e5b3c 35%,#6b5d55 60%,#a3a3a3 100%);}
</style>
</head>
<body>
<main class="flyer">
  <section class="info-column">
    <div class="brand">
      <span class="brand-dot"></span>
      <div class="brand-name">CEDARSTONE BUILDERS</div>
    </div>

    <h1 class="headline">Let’s create<br>your dream<br>outdoor<br>living space!</h1>
    <div class="divider"></div>

    <p class="intro">Discover the endless possibilities for your outdoor space with The Cedarstone Builders Team. Our team of skilled artisans is dedicated to turning your outdoor space into a breathtaking oasis that you’ll love coming home to. Our services include:</p>

    <ul class="services">
      <li>PAVER PATIOS</li>
      <li>PAVER DRIVEWAYS</li>
      <li>RETAINING WALLS</li>
      <li>DECKS &amp; RAILINGS</li>
      <li>POOLS</li>
      <li>OUTDOOR LIGHTING</li>
      <li>FIREPITS &amp; FIREPLACES</li>
    </ul>

    <div class="contact-panel">
      <p class="areas">Our service areas include <strong>Bellevue, Issaquah, Kirkland, Redmond, and Sammamish</strong>. We are trusted, tested and reliable with over 20-years experiences.</p>

      <div class="contact-tag">
        <div class="line"></div>
        <svg width="170" height="22" viewBox="0 0 170 22"><polygon points="0,0 160,0 170,11 160,22 0,22" fill="#ee7a22"/></svg>
        <span>CONTACT US</span>
      </div>

      <div class="phone">
        <svg width="22" height="22" viewBox="0 0 22 22" aria-hidden="true">
          <rect width="22" height="22" fill="#ee7a22"/>
          <path d="M7.2 4.5l2 3.3-1.4 1.5c.8 1.7 2 2.9 3.6 3.7l1.5-1.4 3.3 2-1 2.6c-5.4-.2-9.8-4.6-10-10z" fill="#fff"/>
        </svg>
        <span class="phone-number">206-555-0148</span>
      </div>

      <div class="contact-line email">
        <svg width="15" height="11" viewBox="0 0 15 11" aria-hidden="true">
          <rect width="15" height="11" fill="#ee7a22"/>
          <path d="M0.5 0.8l7 5 7-5" fill="none" stroke="#1b3247" stroke-width="1.3"/>
        </svg>
        <span>info@cedarstonebuilders.com</span>
      </div>
      <div class="contact-line web">
        <svg width="15" height="15" viewBox="0 0 15 15" aria-hidden="true">
          <g fill="none" stroke="#ee7a22" stroke-width="1.1">
            <circle cx="7.5" cy="7.5" r="6.5"/>
            <ellipse cx="7.5" cy="7.5" rx="3" ry="6.5"/>
            <path d="M1 7.5h13M2 4.3h11M2 10.7h11"/>
          </g>
        </svg>
        <span>www.cedarstonebuilders.com</span>
      </div>
    </div>
  </section>

  <section class="gallery">
    <div class="photo deck" role="img" aria-label="Photo of a new composite wood deck with wraparound steps behind a house"></div>
    <div class="photo patio-cover" role="img" aria-label="Photo of a covered patio with cedar posts, stone bar and outdoor furniture on pavers"></div>
    <div class="photo pavilion" role="img" aria-label="Photo of an open pavilion with wood ceiling, stone fireplace and stone counters"></div>
    <div class="photo hillside" role="img" aria-label="Aerial photo of a terraced hillside garden with stone stairs, retaining walls and a paver walkway"></div>
  </section>
</main>
</body>
</html>
```